Business Card Design

We need a new business card design for a company based in Southlake, TX. We provide business consulting services in the information technology / services space. We like variations of the color blue, aqua, black, light tan, and white. Would like "cool" tones. The design should clearly communicate professionalism. Think outside the box - we don't want something "typical". Our company name is "Halvery Consulting, LLC".
Updates

Thank you all for your submissions. We have seen some very creative and inspired designs. We have made a decision and will be moving forward with that design. Appreciate all of the hard work.

Industry/Entity Type

Information Technology

Contact Information for Business Card

Megan Halvery Strube
218 West Birchfold Ridge Dr.
Southlake, TX 76418

```html
<!DOCTYPE html>
<html lang="en">
<head>
<meta charset="utf-8">
<title>Halvery Consulting, LLC – Business Cards</title>
<link rel="stylesheet" href="https://fonts.googleapis.com/css2?family=Open+Sans:wght@400;600;700&display=swap">
<style>
  :root {
    --page-bg: #eeeeee;
    --card-bg: #ffffff;
    --brand-blue: #2a86c0;
    --accent-black: #222222;
    --accent-tan: #e2b999;
    --text-grey: #555555;
    --text-white: #ffffff;
  }
  * { box-sizing: border-box; margin: 0; padding: 0; }
  html, body {
    width: 1200px; height: 828px; overflow: hidden;
    background: var(--page-bg);
    font-family: "Open Sans", Arial, sans-serif;
  }
  .sheet {
    position: relative; width: 1200px; height: 828px;
    display: flex; align-items: center; justify-content: center; gap: 60px;
  }
  .card {
    position: relative; width: 520px; height: 298px;
    background: var(--card-bg);
    box-shadow: 0 4px 14px rgba(0,0,0,0.10);
    overflow: hidden;
  }
  .card--black { --accent: var(--accent-black); --company-colour: var(--brand-blue); }
  .card--tan { --accent: var(--accent-tan); --company-colour: var(--accent-tan); }

  .card__company {
    position: absolute; top: 42px; right: 34px; text-align: left;
  }
  .company-name {
    font-weight: 700; font-size: 18px; color: var(--company-colour); letter-spacing: -0.2px;
  }
  .company-tagline {
    font-size: 12.5px; color: var(--text-grey); margin-left: 10px;
  }

  .card__person {
    position: absolute; top: 116px; left: 0; display: flex; align-items: flex-start;
  }
  .person-marker {
    width: 26px; height: 34px; background: var(--brand-blue); margin-right: 8px;
  }
  .person-name { font-weight: 700; font-size: 15.5px; color: var(--brand-blue); line-height: 1.2; }
  .person-title { font-size: 12.5px; color: var(--text-grey); }

  .contact {
    position: absolute; display: flex; align-items: center; gap: 7px;
    font-size: 12.5px; color: var(--text-grey);
  }
  .contact svg { width: 18px; height: 18px; flex: none; }
  .contact--phone { left: 26px; top: 194px; }
  .contact--mobile { left: 196px; top: 170px; }
  .contact--mail { left: 346px; top: 150px; }

  .card__bands { position: absolute; inset: 0; width: 100%; height: 100%; }
  .band-blue { fill: var(--brand-blue); }
  .band-accent { fill: var(--accent); }

  .contact--address { left: 22px; top: 252px; color: var(--text-white); font-size: 11.5px; }
  .card__web {
    position: absolute; left: 372px; top: 212px; width: 140px;
    font-size: 12px; color: var(--text-white);
  }
  .card--tan .card__web { color: var(--text-grey); }
</style>
</head>
<body>
<main class="sheet">

  <article class="card card--black">
    <svg class="card__bands" viewBox="0 0 520 298" aria-hidden="true">
      <polygon class="band-blue" points="0,236 352,200 338,298 0,298"/>
      <polygon class="band-accent" points="362,180 520,164 520,298 348,298"/>
    </svg>
    <div class="card__company">
      <div class="company-name">Halvery Consulting, LLC</div>
      <div class="company-tagline">Business Consulting Services</div>
    </div>
    <div class="card__person">
      <div class="person-marker"></div>
      <div>
        <div class="person-name">Megan Halvery Strube</div>
        <div class="person-title">Consultant, Manager</div>
      </div>
    </div>
    <div class="contact contact--phone">
      <svg viewBox="0 0 20 20"><circle cx="10" cy="10" r="10" fill="#2a86c0"/><path d="M7 5.5l1.6 2.4-1 1c.6 1.3 1.5 2.2 2.6 2.8l1-1 2.3 1.6-.9 1.8c-3.3-.4-6.2-3.3-6.6-6.6z" fill="#fff"/></svg>
      <span>01 52 70 14 86</span>
    </div>
    <div class="contact contact--mobile">
      <svg viewBox="0 0 20 20"><circle cx="10" cy="10" r="10" fill="#2a86c0"/><rect x="7" y="4.5" width="6" height="11" rx="1" fill="none" stroke="#fff" stroke-width="1.3"/></svg>
      <span>06 31 47 20 68</span>
    </div>
    <div class="contact contact--mail">
      <svg viewBox="0 0 20 20"><circle cx="10" cy="10" r="10" fill="#2a86c0"/><rect x="5" y="6.5" width="10" height="7" fill="none" stroke="#fff" stroke-width="1.2"/><path d="M5 6.5l5 4 5-4" fill="none" stroke="#fff" stroke-width="1.2"/></svg>
      <span>megan@halvery.com</span>
    </div>
    <div class="contact contact--address">
      <svg viewBox="0 0 20 20"><circle cx="10" cy="10" r="10" fill="#fff"/><path d="M10 4.5a3.5 3.5 0 0 0-3.5 3.5c0 2.6 3.5 7 3.5 7s3.5-4.4 3.5-7A3.5 3.5 0 0 0 10 4.5zm0 5a1.4 1.4 0 1 1 0-2.8 1.4 1.4 0 0 1 0 2.8z" fill="#2a86c0"/></svg>
      <span>218 West Birchfold Ridge Dr. 76418 Southlake</span>
    </div>
    <div class="card__web">www.halveryconsult.com</div>
  </article>

  <article class="card card--tan">
    <svg class="card__bands" viewBox="0 0 520 298" aria-hidden="true">
      <polygon class="band-blue" points="0,236 352,200 338,298 0,298"/>
      <polygon class="band-accent" points="362,180 520,164 520,298 348,298"/>
    </svg>
    <div class="card__company">
      <div class="company-name">Halvery Consulting, LLC</div>
      <div class="company-tagline">Business Consulting Services</div>
    </div>
    <div class="card__person">
      <div class="person-marker"></div>
      <div>
        <div class="person-name">Megan Halvery Strube</div>
        <div class="person-title">Consultant, Manager</div>
      </div>
    </div>
    <div class="contact contact--phone">
      <svg viewBox="0 0 20 20"><circle cx="10" cy="10" r="10" fill="#2a86c0"/><path d="M7 5.5l1.6 2.4-1 1c.6 1.3 1.5 2.2 2.6 2.8l1-1 2.3 1.6-.9 1.8c-3.3-.4-6.2-3.3-6.6-6.6z" fill="#fff"/></svg>
      <span>01 52 70 14 86</span>
    </div>
    <div class="contact contact--mobile">
      <svg viewBox="0 0 20 20"><circle cx="10" cy="10" r="10" fill="#2a86c0"/><rect x="7" y="4.5" width="6" height="11" rx="1" fill="none" stroke="#fff" stroke-width="1.3"/></svg>
      <span>06 31 47 20 68</span>
    </div>
    <div class="contact contact--mail">
      <svg viewBox="0 0 20 20"><circle cx="10" cy="10" r="10" fill="#2a86c0"/><rect x="5" y="6.5" width="10" height="7" fill="none" stroke="#fff" stroke-width="1.2"/><path d="M5 6.5l5 4 5-4" fill="none" stroke="#fff" stroke-width="1.2"/></svg>
      <span>megan@halvery.com</span>
    </div>
    <div class="contact contact--address">
      <svg viewBox="0 0 20 20"><circle cx="10" cy="10" r="10" fill="#fff"/><path d="M10 4.5a3.5 3.5 0 0 0-3.5 3.5c0 2.6 3.5 7 3.5 7s3.5-4.4 3.5-7A3.5 3.5 0 0 0 10 4.5zm0 5a1.4 1.4 0 1 1 0-2.8 1.4 1.4 0 0 1 0 2.8z" fill="#2a86c0"/></svg>
      <span>218 West Birchfold Ridge Dr. 76418 Southlake</span>
    </div>
    <div class="card__web">www.halveryconsult.com</div>
  </article>

</main>
</body>
</html>
```